Business Card Design - Property Management & Real Estate Services

I need a business card design for my company that I can print ZEPLA Cards. The company is called Brindle Management Company. It is a property management and real estate company. The design has to be clean and modern. I need two versions. One for my employee and one for me. However, the design will be the same, just different text. You can get a feel for the company by looking at our website at www.brindlemanagement.example.

Industry/Entity Type

Property Management

Contact Information for Business Card

I will be using ZEPLA.com to print my cards. I will most likely use the rounded edges card. I need two versions, however, they will be the same design. I need one for me and my employee.

Colors
3276b5
33a6d7

Requirements
Must have
• Company Logo
• Name of person
• Property Management & Real Estate Service
• Phone
• Email
• Website
• Address
• A space to place a QR code

```html
<!DOCTYPE html>
<html lang="en">
<head>
<meta charset="utf-8">
<title>Brindle Management – Business Card</title>
<link href="https://fonts.googleapis.com/css2?family=Roboto:wght@400;500;700&display=swap" rel="stylesheet">
<style>
  :root {
    --backdrop: #c9cacb;
    --front-blue: #6699cc;
    --deep-blue: #1b55a3;
    --mark-blue: #2a5ea8;
    --accent-line: #5b8fd0;
    --paper: #f4f5f6;
    --white: #ffffff;
  }
  * { margin: 0; padding: 0; box-sizing: border-box; }
  html, body { width: 1200px; height: 852px; overflow: hidden; }
  body {
    background: var(--backdrop);
    font-family: "Roboto", Arial, sans-serif;
    position: relative;
  }
  .card {
    position: absolute;
    top: 281px;
    width: 490px;
    height: 290px;
    border-radius: 16px;
    overflow: hidden;
    box-shadow: 0 6px 14px rgba(0,0,0,0.18);
  }
  .card--front { left: 85px; background: var(--front-blue); }
  .card--back { left: 625px; background: var(--paper); }

  .wordmark {
    color: var(--mark-blue);
    font-weight: 500;
    text-transform: uppercase;
    line-height: 1;
  }
  .card--front .wordmark {
    position: absolute;
    left: 0; right: 0; top: 102px;
    text-align: center;
  }
  .card--front .wordmark__name { font-size: 52px; letter-spacing: 2px; display: block; }
  .card--front .wordmark__sub { font-size: 13px; letter-spacing: 9px; display: block; margin-top: 8px; }

  .back-band { position: absolute; inset: 0; }

  .card--back .wordmark {
    position: absolute;
    left: 30px; top: 46px;
    display: flex; align-items: center; gap: 10px;
  }
  .wordmark__square { width: 26px; height: 26px; border: 2px solid var(--mark-blue); }
  .card--back .wordmark__name { font-size: 30px; letter-spacing: 1px; display: block; }
  .card--back .wordmark__sub { font-size: 9px; letter-spacing: 5px; display: block; margin-top: 4px; }

  .contact {
    position: absolute;
    left: 30px; top: 146px;
    color: var(--white);
  }
  .contact__name { font-size: 19px; font-weight: 700; }
  .contact__role { font-size: 12px; margin-top: 3px; margin-bottom: 10px; }
  .contact__row { display: flex; align-items: center; gap: 8px; font-size: 12px; line-height: 19px; }
  .contact__row svg { width: 11px; height: 11px; flex: none; }
  .contact__address { font-size: 12px; line-height: 19px; }
</style>
</head>
<body>

<section class="card card--front" aria-label="Card front">
  <div class="wordmark">
    <span class="wordmark__name">Brindle</span>
    <span class="wordmark__sub">Management</span>
  </div>
</section>

<section class="card card--back" aria-label="Card back">
  <svg class="back-band" viewBox="0 0 490 290" preserveAspectRatio="none" aria-hidden="true">
    <polygon points="0,135 300,135 300,105 490,105 490,290 0,290" fill="var(--deep-blue)"/>
    <line x1="0" y1="280" x2="490" y2="280" stroke="var(--accent-line)" stroke-width="4"/>
  </svg>

  <div class="wordmark">
    <span class="wordmark__square"></span>
    <span>
      <span class="wordmark__name">Brindle</span>
      <span class="wordmark__sub">Management</span>
    </span>
  </div>

  <div class="contact">
    <p class="contact__name">Mateo R. Salinas</p>
    <p class="contact__role">Founder</p>
    <p class="contact__row">
      <svg viewBox="0 0 12 12"><path d="M2 1h3l1 3-1.5 1a6 6 0 0 0 2.5 2.5L8 6l3 1v3a1 1 0 0 1-1 1A9 9 0 0 1 1 2a1 1 0 0 1 1-1z" fill="#fff"/></svg>
      (305) 555-0148
    </p>
    <p class="contact__row">
      <svg viewBox="0 0 12 12"><rect x="1" y="2.5" width="10" height="7" fill="#fff"/><path d="M1 2.5l5 4 5-4" stroke="#1b55a3" fill="none"/></svg>
      mateo@brindlemanagement.example
    </p>
    <p class="contact__row">
      <svg viewBox="0 0 12 12"><circle cx="6" cy="6" r="5" fill="none" stroke="#fff"/><path d="M1 6h10M6 1c-3 3-3 7 0 10M6 1c3 3 3 7 0 10" stroke="#fff" fill="none"/></svg>
      www.brindlemanagement.example
    </p>
    <p class="contact__address">480 Harbor Ave #210 Miami, FL 33130</p>
  </div>
</section>

</body>
</html>
```